Business Card for Multi-Brand Sportswear Company

We are looking for a business card which represents our company and the multiple brands within it.

The company: Fen Athletics (LTD)
The brands: Fen, TavaPuni, ElmStretch, Grit and Rain

Employees using these cards would be representing Fen Athletics, rather than any of the individual brands. You will see a current design within the uploaded files, to give some inspiration. The actual text of the brands is not necessary, but the logos should be on there is some format.

Our creative minds on this are stretched, so we are looking for someone to make this their own, and show us what a good business card should look like.

We may like to get these printed with spot gloss, so keep that in mind with your designs.

www.fenathletics.co.uk

Industry/Entity Type

Business

Contact Information for Business Card

Leo Pemberton-Hale
Operations Manager
(+44) 1632 960 418
Leo@fenathletics.co.uk
www.fenathletics.co.uk

Font styles to use
Sans Serif
Other font styles liked:
• Eurostile

Colors
ffffff

Requirements
Nice to have
• Dark (black) background

```html
<!DOCTYPE html>
<html lang="en">
<head>
<meta charset="utf-8">
<title>Fen Athletics – Business Card</title>
<link rel="stylesheet" href="https://fonts.googleapis.com/css2?family=Exo+2:wght@400;600&family=Arimo:wght@400;700&display=swap">
<style>
  :root {
    --stage: #ececec;
    --card-dark: #2c2c2c;
    --card-dark-deep: #1f1f1f;
    --card-light: #ffffff;
    --card-light-shade: #e9e9e9;
    --ink: #111111;
    --ink-soft: #6b6b6b;
    --accent: #d71920;
    --on-dark: #ffffff;
    --on-dark-soft: #bdbdbd;
    --brand-mark: #8a8a8a;
  }
  * { margin: 0; padding: 0; box-sizing: border-box; }
  html, body { width: 1200px; height: 586px; overflow: hidden; }
  body { background: var(--stage); position: relative; font-family: "Arimo", sans-serif; }

  .card { position: absolute; top: 129px; width: 502px; height: 301px; overflow: hidden; }
  .card-texture { position: absolute; inset: 0; }

  .card-front { left: 66px; background: var(--card-dark); }
  .card-front .card-texture { background: linear-gradient(135deg, var(--card-dark) 0%, var(--card-dark-deep) 50%, var(--card-dark) 100%); }

  .card-back { left: 608px; background: var(--card-light); }
  .card-back .card-texture { background: linear-gradient(135deg, var(--card-light) 0%, var(--card-light-shade) 55%, var(--card-light) 100%); }

  .wordmark { position: absolute; font-family: "Exo 2", sans-serif; }
  .wordmark-name { display: block; font-weight: 400; letter-spacing: 0.5px; line-height: 1; }
  .wordmark-tagline { display: block; font-weight: 400; letter-spacing: 2px; line-height: 1; }

  .card-front .wordmark { left: 0; right: 0; top: 118px; text-align: center; }
  .card-front .wordmark-name { font-size: 42px; color: var(--on-dark); }
  .card-front .wordmark-tagline { font-size: 11px; color: var(--on-dark-soft); margin-top: 8px; letter-spacing: 3px; }

  .card-back .wordmark { left: 30px; top: 28px; }
  .card-back .wordmark-name { font-size: 30px; color: var(--ink); }
  .card-back .wordmark-tagline { font-size: 7.5px; color: var(--ink-soft); margin-top: 5px; letter-spacing: 1.6px; }

  .holder { position: absolute; right: 32px; top: 143px; text-align: right; }
  .holder-name { font-size: 16px; font-weight: 700; color: var(--ink); }
  .holder-role { font-size: 11.5px; color: var(--ink); margin-top: 8px; }
  .holder-rule { position: absolute; left: 26px; top: 171px; width: 334px; height: 3px; background: var(--accent); }

  .contact-list { position: absolute; left: 30px; top: 187px; list-style: none; }
  .contact-item { display: flex; align-items: center; height: 25px; font-size: 11.5px; color: var(--ink); }
  .contact-item svg { width: 13px; height: 12px; margin-right: 8px; fill: var(--accent); }
  .address { position: absolute; left: 31px; top: 261px; font-size: 12.5px; font-weight: 700; color: var(--ink); }

  .brand-row { position: absolute; right: 28px; top: 262px; display: flex; gap: 9px; align-items: center; }
  .brand-name { font-family: "Exo 2", sans-serif; font-size: 9px; font-weight: 600; color: var(--brand-mark); }
</style>
</head>
<body>
  <section class="card card-front" aria-label="Card front">
    <div class="card-texture" role="img" aria-label="Faceted low-poly charcoal texture"></div>
    <div class="wordmark">
      <span class="wordmark-name">Fen Athletics</span>
      <span class="wordmark-tagline">PERFORMANCE WEAR</span>
    </div>
  </section>

  <section class="card card-back" aria-label="Card back">
    <div class="card-texture" role="img" aria-label="Faceted low-poly white texture"></div>
    <div class="wordmark">
      <span class="wordmark-name">Fen Athletics</span>
      <span class="wordmark-tagline">PERFORMANCE WEAR</span>
    </div>

    <div class="holder">
      <p class="holder-name">Owen Radcliffe</p>
      <p class="holder-role">Managing Director</p>
    </div>
    <div class="holder-rule"></div>

    <ul class="contact-list">
      <li class="contact-item">
        <svg viewBox="0 0 13 12" aria-hidden="true"><path d="M1 4c0-2 2-3 5.5-3S12 2 12 4v1H9V3.5H4V5H1z"/><rect x="2" y="6" width="9" height="5" rx="1"/></svg>
        +44 (0)1632 960771
      </li>
      <li class="contact-item">
        <svg viewBox="0 0 13 12" aria-hidden="true"><rect x="3" y="0.5" width="7" height="3"/><rect x="0.5" y="4" width="12" height="5" rx="1"/><rect x="3" y="8" width="7" height="3.5"/></svg>
        (555) 014-2290
      </li>
      <li class="contact-item">
        <svg viewBox="0 0 13 12" aria-hidden="true"><path d="M0.5 2h12v8h-12z M1.5 3l5 4 5-4" stroke="#fff" stroke-width="0.8"/></svg>
        owen@fenathletics.co.uk
      </li>
    </ul>
    <p class="address">Marsh Lane, Ely Fenside, CB7 4QX</p>

    <div class="brand-row" aria-label="Group brands">
      <span class="brand-name">TavaPuni</span>
      <span class="brand-name">Grit and Rain</span>
      <span class="brand-name">ElmStretch</span>
      <span class="brand-name">Fen</span>
    </div>
  </section>
</body>
</html>
```